Marwick Law Letterhead

We need a new letterhead design for a Law Firm. The address for the law firm is 1475 Calloway Street, Suite 210, Houston, Texas 77041. Phone Number: 832-361-9027; Fax Number: 832-614-7359. The logo is uploaded to the project.

```html
<!DOCTYPE html>
<html lang="en">
<head>
<meta charset="utf-8">
<title>Marwick Law Letterhead</title>
<link rel="stylesheet" href="https://fonts.googleapis.com/css2?family=Libre+Baskerville:wght@400&family=Mulish:wght@400;500&display=swap">
<style>
  :root {
    --backdrop: #e8e8e8;
    --paper: #ffffff;
    --navy: #1c2b5a;
    --accent-red: #c8202f;
    --rule-red: #9b2a35;
    --ink: #1a1a1a;
  }
  * { margin: 0; padding: 0; box-sizing: border-box; }
  html, body {
    width: 1154px;
    height: 1200px;
    overflow: hidden;
    background: var(--backdrop);
  }
  .letterhead {
    position: absolute;
    left: 170px;
    top: 30px;
    width: 815px;
    height: 1140px;
    background: var(--paper);
    box-shadow: 0 6px 22px rgba(0, 0, 0, 0.18);
  }
  .brand {
    position: absolute;
    left: 34px;
    top: 66px;
    display: flex;
    align-items: center;
    gap: 12px;
  }
  .brand-dot {
    width: 14px;
    height: 14px;
    border-radius: 50%;
    background: var(--navy);
  }
  .brand-name {
    font-family: "Libre Baskerville", Georgia, serif;
    font-weight: 400;
    font-size: 32px;
    letter-spacing: 0.5px;
    color: var(--navy);
    line-height: 1;
  }
  .footer {
    position: absolute;
    left: 30px;
    right: 30px;
    bottom: 28px;
    font-family: "Mulish", Arial, sans-serif;
    font-size: 14px;
    color: var(--ink);
  }
  .footer-rule {
    height: 1px;
    background: var(--rule-red);
    margin-bottom: 17px;
  }
  .address {
    font-style: normal;
    line-height: 17.5px;
    margin-bottom: 12px;
  }
  .contact {
    list-style: none;
  }
  .contact li {
    display: flex;
    align-items: center;
    gap: 9px;
    line-height: 20px;
  }
  .contact svg {
    width: 13px;
    height: 13px;
    fill: var(--accent-red);
    flex: none;
  }
</style>
</head>
<body>
  <main class="letterhead">
    <header class="brand">
      <span class="brand-dot"></span>
      <span class="brand-name">Marwick Law</span>
    </header>

    <footer class="footer">
      <div class="footer-rule"></div>
      <address class="address">
        1475 Calloway Street,<br>
        Suite 210, Houston,<br>
        Texas 77041
      </address>
      <ul class="contact">
        <li class="contact-phone">
          <svg viewBox="0 0 24 24" aria-hidden="true"><path d="M6.6 10.8a15.1 15.1 0 0 0 6.6 6.6l2.2-2.2a1 1 0 0 1 1-.25 11.4 11.4 0 0 0 3.6.57 1 1 0 0 1 1 1V20a1 1 0 0 1-1 1A17 17 0 0 1 3 4a1 1 0 0 1 1-1h3.5a1 1 0 0 1 1 1c0 1.25.2 2.45.57 3.57a1 1 0 0 1-.25 1z"/></svg>
          832-361-9027
        </li>
        <li class="contact-fax">
          <svg viewBox="0 0 24 24" aria-hidden="true"><path d="M6 2h12v5H6zM4 8h16a2 2 0 0 1 2 2v7h-4v5H6v-5H2v-7a2 2 0 0 1 2-2zm4 8v4h8v-4z"/></svg>
          832-614-7359
        </li>
      </ul>
    </footer>
  </main>
</body>
</html>
```